Roll up corner and Three fold flyer

I need a roll up corner and a three-fold flyer that follow the same design:

I would like to advertise Hospitality, Tourism and Culinary internships in China, Spain, and Australia.

I am attaching some samples:

1.- A roll up corner sample
2.- 4 picuters of a Three-Fold flyer of a company who also does internships in Hospitality. And I really like its flyers.
3.- Three PDF files (Australia, Spain and China) with basic information I would like in the three fold or/and the roll up corner.

Three fold size: A normal letter format
Roll up corner: 85cm x 200 cm

Target Market(s)

Students

Industry/Entity Type

Tourism

Requirements
Must have
• Company name: Northwind Ventures

```html
<!DOCTYPE html>
<html lang="en">
<head>
<meta charset="utf-8">
<title>Northwind Ventures – Hospitality Internships Roll-up</title>
<link rel="stylesheet" href="https://fonts.googleapis.com/css2?family=Lato:wght@300;400&display=swap">
<style>
  :root {
    --backdrop: #e4e4e6;
    --ink-dark: #333333;
    --amber: #d9930c;
    --paper: #ffffff;
    --rim: #e3e3e5;
    --soft-shade: #dcdcde;
    --body-grey: #a3a3a3;
    --photo-warm: #e9dcc6;
    --photo-deep: #6b4e36;
  }
  html, body {
    margin: 0;
    padding: 0;
    width: 1200px;
    height: 1200px;
    overflow: hidden;
    background: var(--backdrop);
  }
  .rollup {
    position: absolute;
    left: 349px;
    top: 40px;
    width: 502px;
    height: 1121px;
    display: block;
  }
  .rollup__brand {
    font-family: "Lato", sans-serif;
    font-weight: 300;
    font-size: 24px;
    letter-spacing: 4px;
    fill: var(--paper);
  }
  .rollup__headline {
    font-family: "Lato", sans-serif;
    font-weight: 300;
    font-size: 57px;
    letter-spacing: 1px;
    fill: var(--amber);
  }
  .rollup__body {
    font-family: "Lato", sans-serif;
    font-weight: 400;
    font-size: 14.5px;
    fill: var(--body-grey);
  }
</style>
</head>
<body>
<svg class="rollup" viewBox="0 0 436 974" xmlns="http://www.w3.org/2000/svg">
  <defs>
    <radialGradient id="photoTone" cx="0.6" cy="0.4" r="0.7">
      <stop offset="0" stop-color="var(--photo-warm)"/>
      <stop offset="0.6" stop-color="#c9ab87"/>
      <stop offset="1" stop-color="var(--photo-deep)"/>
    </radialGradient>
    <clipPath id="photoClip"><circle cx="216" cy="388" r="186"/></clipPath>
  </defs>

  <!-- amber base -->
  <rect class="rollup__base" width="436" height="974" fill="var(--amber)"/>

  <!-- dark header band with white divider curve -->
  <path class="rollup__divider" d="M0 34 C120 96 300 142 436 144 V150 C300 148 120 104 0 44 Z" fill="var(--paper)"/>
  <path class="rollup__header" d="M0 0 H436 V138 C300 136 120 92 0 30 Z" fill="var(--ink-dark)"/>

  <!-- white sweep -->
  <path class="rollup__sweep-shade" d="M436 196 C250 226 60 430 0 640 V952 C150 948 330 906 436 818 Z" fill="var(--soft-shade)"/>
  <path class="rollup__sweep" d="M436 202 C250 232 72 440 14 640 C8 700 8 760 0 800 V944 C150 940 330 900 436 826 Z" fill="var(--paper)"/>

  <!-- brand -->
  <text class="rollup__brand" x="412" y="54" text-anchor="end">NORTHWIND</text>
  <text class="rollup__brand" x="412" y="88" text-anchor="end">VENTURES</text>

  <!-- photo frame -->
  <circle class="rollup__photo-rim" cx="216" cy="388" r="198" fill="var(--rim)"/>
  <g role="img" aria-label="Photo of a smiling hotel receptionist in a dark blazer standing in a restaurant">
    <rect x="30" y="202" width="372" height="372" clip-path="url(#photoClip)" fill="url(#photoTone)"/>
  </g>

  <!-- headline -->
  <text class="rollup__headline" x="51" y="691">HOSPITALITY</text>
  <text class="rollup__headline" x="51" y="759">INTERNSHIPS</text>

  <!-- body copy -->
  <text class="rollup__body" x="28" y="794" textLength="384" lengthAdjust="spacingAndGlyphs">Lorem ipsum dolor sit amet, quo et mazim in ix ei idqu</text>
  <text class="rollup__body" x="28" y="814" textLength="386" lengthAdjust="spacingAndGlyphs">ix ei idque intellegat referrentur. Suas deterr  uri disput</text>
  <text class="rollup__body" x="28" y="834" textLength="364" lengthAdjust="spacingAndGlyphs">disputando ex usu. Justo epicurei tacimat atqui qua</text>
</svg>
</body>
</html>
```